Business Card Design

We are a residential half way house for the addict ,the alcoholic and dual diagnosed in recovery.
i house both men and woman age 18+

Industry/Entity Type

Residential

```html
<!DOCTYPE html>
<html lang="en">
<head>
<meta charset="utf-8">
<title>Marlowe's Family Sober House – Business Card</title>
<link href="https://fonts.googleapis.com/css2?family=Parisienne&family=Raleway:wght@300;400&display=swap" rel="stylesheet">
<style>
  :root {
    --backdrop: #d9d6d1;
    --card-black: #0d0d0d;
    --card-sheen: #2a2a2a;
    --text-white: #f4f4f4;
    --strip-white: #ececec;
    --tile-border: #1a1a1a;
  }
  html, body {
    margin: 0;
    width: 1200px;
    height: 892px;
    overflow: hidden;
    background: var(--backdrop);
  }
  .card {
    position: absolute;
    left: 75px;
    top: 146px;
    width: 1050px;
    height: 600px;
    background: linear-gradient(160deg, var(--card-sheen) 0%, var(--card-black) 45%, var(--card-black) 100%);
    box-shadow: 0 12px 30px rgba(0,0,0,0.35);
    color: var(--text-white);
    font-family: "Raleway", sans-serif;
    overflow: hidden;
  }
  .brand {
    position: absolute;
    left: 60px;
    top: 120px;
    font-family: "Parisienne", cursive;
  }
  .brand-name {
    font-size: 62px;
    line-height: 1;
  }
  .brand-line {
    font-size: 38px;
    line-height: 1.1;
    margin-left: 50px;
  }
  .fax {
    position: absolute;
    left: 190px;
    top: 290px;
    font-size: 22px;
    font-weight: 300;
  }
  .contact {
    position: absolute;
    right: 60px;
    top: 40px;
    text-align: right;
    font-weight: 300;
  }
  .contact-name {
    font-size: 42px;
    font-weight: 300;
    margin: 0;
  }
  .contact-role {
    font-size: 22px;
    margin: 2px 0 0;
  }
  .contact-note {
    font-size: 22px;
    margin: 2px 0 18px;
  }
  .contact-line {
    font-size: 24px;
    margin: 2px 0;
  }
  .photo-strip {
    position: absolute;
    left: 0;
    top: 350px;
    width: 100%;
    height: 168px;
    background: var(--strip-white);
    display: flex;
    justify-content: space-between;
    align-items: center;
    padding: 0 16px;
    box-sizing: border-box;
  }
  .photo-tile {
    width: 190px;
    height: 140px;
    border: 4px solid var(--tile-border);
    box-sizing: border-box;
  }
  .photo-grill { background: linear-gradient(135deg, #3b2a20, #8a5a34 50%, #e08a2a); }
  .photo-campfire { background: radial-gradient(circle at 55% 55%, #ffd27a 0%, #e0801f 25%, #3a1a0a 60%, #0b0604 100%); }
  .photo-canoe { background: linear-gradient(180deg, #7aa068 0%, #c9d6b8 45%, #c8503a 80%, #8a3a2a 100%); }
  .photo-fishing { background: linear-gradient(180deg, #e8d6b0 0%, #c9a26a 45%, #4a3a28 100%); }
  .photo-sports { background: radial-gradient(circle at 50% 50%, #e07a30 0%, #d04040 35%, #8fb8d8 65%, #f4f4f4 100%); }
  .address {
    position: absolute;
    right: 60px;
    bottom: 30px;
    font-size: 26px;
    font-weight: 400;
  }
</style>
</head>
<body>
  <div class="card">
    <div class="brand">
      <div class="brand-name">Marlowe's</div>
      <div class="brand-line">Family Sober House Inc</div>
    </div>
    <div class="fax">Fax : (555) 014-8893</div>

    <div class="contact">
      <p class="contact-name">Dana Whitfield</p>
      <p class="contact-role">Owner</p>
      <p class="contact-note">(15 yrs.in recovery)</p>
      <p class="contact-line">(555) 014-2270</p>
      <p class="contact-line">(555) 014-2271</p>
      <p class="contact-line">danawhitfield@mailbox.net</p>
    </div>

    <div class="photo-strip">
      <div class="photo-tile photo-grill" role="img" aria-label="Burgers cooking on a flaming grill"></div>
      <div class="photo-tile photo-campfire" role="img" aria-label="Friends gathered around a campfire at night"></div>
      <div class="photo-tile photo-canoe" role="img" aria-label="Family paddling a red canoe on a lake"></div>
      <div class="photo-tile photo-fishing" role="img" aria-label="Person fishing from a boat at sunset"></div>
      <div class="photo-tile photo-sports" role="img" aria-label="Hand holding a bundle of sports balls"></div>
    </div>

    <div class="address">4127 Palmetto Rd. Harbor Point,Fla 30045</div>
  </div>
</body>
</html>
```